Marwick Family Chiropractic Stationary

The letterhead and business card must have our logo.
We would like to see the logo used in different ways ( It can be expanded upon in the stationary.)
Please use the the same or similar colors.
Must be eye catching and memorable.
Must be easy to read

Reason: The doctor has been too busy to make any final decisions. He would like to give himself a little more time.

Target Market(s)

Chiropractic Healthcare

Industry/Entity Type

Business

Requirements
Must have
• Dr. Leonard Marwick D.C.
Chiropractor

603-555-0183

417 Birchfield Road, 2nd Floor
Elmridge, NH 06091

drmarwick@marwickspine.example
www.marwickspine.example
www.facebook.com/MarwickFamilySpine
Should not have
• should not be difficult to read

```html
<!DOCTYPE html>
<html lang="en">
<head>
<meta charset="utf-8">
<title>Marwick Family Chiropractic – Business Cards</title>
<link href="https://fonts.googleapis.com/css2?family=Ubuntu:wght@500;700&family=Arimo:wght@400;700&display=swap" rel="stylesheet">
<style>
  :root{
    --backdrop:#9a9a9a;
    --card-black:#050505;
    --leaf-green:#2f6b35;
    --brand-lime:#a7c95c;
    --brand-taupe:#7e7161;
    --tag-taupe:#9a8a74;
    --name-yellow:#e6e619;
    --role-lime:#c3dc5a;
    --ink-white:#ffffff;
  }
  *{margin:0;padding:0;box-sizing:border-box}
  html,body{width:1200px;height:740px;overflow:hidden;background:var(--backdrop)}
  .sheet{position:relative;width:1200px;height:740px}
  .card{position:absolute}
  .card-shape{position:absolute;inset:0;display:block}
  .card--front{left:34px;top:36px;width:563px;height:317px}
  .card--back-dark{left:607px;top:36px;width:550px;height:319px}
  .card--back-taupe{left:302px;top:387px;width:552px;height:319px}

  .mark{position:absolute;border-radius:50%}
  .wordmark{position:absolute;text-align:center;font-family:"Ubuntu",sans-serif;font-weight:700;line-height:1}
  .wordmark__name{display:block;font-size:38px;letter-spacing:1px;color:var(--brand-lime)}
  .wordmark__tag{display:block;font-size:15.5px;letter-spacing:.6px;margin-top:9px;color:var(--tag-taupe)}

  .card--front .mark{left:76px;top:58px;width:130px;height:130px;background:var(--brand-lime)}
  .card--front .wordmark{left:10px;top:198px;width:262px}

  .contact{position:absolute;right:14px;top:56px;text-align:right;font-family:"Arimo",sans-serif;color:var(--ink-white);font-size:12.5px;line-height:18.6px}
  .contact__name{font-weight:700;color:var(--name-yellow);font-size:13px;line-height:16px}
  .contact__role{color:var(--role-lime);font-size:12px;line-height:15px;margin-bottom:17px}
  .contact__line{display:flex;justify-content:flex-end;align-items:center;gap:5px}
  .contact__line svg{width:10px;height:10px;flex:none}
  .contact__social-dot{width:8px;height:8px;background:#3b5bb0;flex:none}
  .contact__address{margin-top:13px;line-height:19.5px}

  .card--back-dark .mark{left:209px;top:53px;width:130px;height:130px;background:var(--brand-lime)}
  .card--back-dark .wordmark{left:130px;top:192px;width:288px}
  .site{position:absolute;font-family:"Arimo",sans-serif;color:var(--ink-white);font-size:14px;letter-spacing:2.4px;text-align:center;white-space:nowrap}
  .card--back-dark .site{left:100px;width:348px;top:270px}

  .card--back-taupe .mark{left:201px;top:38px;width:150px;height:150px;background:var(--ink-white)}
  .card--back-taupe .wordmark{left:130px;width:292px;top:206px}
  .card--back-taupe .wordmark__name{font-size:30px;color:var(--ink-white)}
  .card--back-taupe .site{left:100px;width:352px;top:250px}
</style>
</head>
<body>
<main class="sheet">

  <section class="card card--front">
    <svg class="card-shape" viewBox="0 0 563 317" aria-hidden="true">
      <path d="M0,0 H563 V317 H0 Z" fill="var(--card-black)"/>
      <path d="M372,317 C300,285 262,205 292,140 C330,62 448,18 552,0 L563,0 L563,317 Z" fill="var(--leaf-green)"/>
    </svg>
    <div class="mark" role="img" aria-label="Practice logo mark"></div>
    <div class="wordmark">
      <span class="wordmark__name">MARWICK</span>
      <span class="wordmark__tag">FAMILY CHIROPRACTIC</span>
    </div>
    <div class="contact">
      <p class="contact__name">Dr. Leonard Marwick D.C.</p>
      <p class="contact__role">Chiropractor</p>
      <p class="contact__line">
        <svg viewBox="0 0 10 10"><path d="M2,1 L4,1 L4.6,3 L3.4,3.8 C4,5.2 4.8,6 6.2,6.6 L7,5.4 L9,6 L9,8 C5,8.6 1.4,5 2,1 Z" fill="none" stroke="#fff" stroke-width="0.9"/></svg>
        603-555-0183</p>
      <p class="contact__line"><span class="contact__social-dot"></span>MarwickFamilySpine</p>
      <p class="contact__line">
        <svg viewBox="0 0 10 10"><circle cx="5" cy="5" r="4" fill="none" stroke="#fff" stroke-width="0.9"/><ellipse cx="5" cy="5" rx="1.8" ry="4" fill="none" stroke="#fff" stroke-width="0.8"/><path d="M1,5 H9" stroke="#fff" stroke-width="0.8"/></svg>
        www.marwickspine.example</p>
      <p class="contact__line">
        <svg viewBox="0 0 10 10"><rect x="1" y="2.5" width="8" height="5.5" fill="none" stroke="#fff" stroke-width="0.9"/><path d="M1,2.5 L5,5.8 L9,2.5" fill="none" stroke="#fff" stroke-width="0.9"/></svg>
        mymarwick@marwickspine.example</p>
      <p class="contact__address">417 Birchfield Road<br>Suite 2B, Elmridge<br>NH 06091</p>
    </div>
  </section>

  <section class="card card--back-dark">
    <svg class="card-shape" viewBox="0 0 550 319" aria-hidden="true">
      <path d="M0,0 H515 C538,4 550,28 550,60 V190 C550,265 480,319 385,319 H0 Z" fill="var(--card-black)"/>
    </svg>
    <div class="mark" role="img" aria-label="Practice logo mark"></div>
    <div class="wordmark">
      <span class="wordmark__name">MARWICK</span>
      <span class="wordmark__tag">FAMILY CHIROPRACTIC</span>
    </div>
    <p class="site">www.marwickspine.example</p>
  </section>

  <section class="card card--back-taupe">
    <svg class="card-shape" viewBox="0 0 552 319" aria-hidden="true">
      <path d="M0,0 H520 C540,6 552,30 552,62 V185 C552,260 490,319 420,319 H0 Z" fill="var(--brand-taupe)"/>
    </svg>
    <div class="mark" role="img" aria-label="Large practice logo mark"></div>
    <div class="wordmark">
      <span class="wordmark__name">MARWICK</span>
    </div>
    <p class="site">www.marwickspine.example</p>
  </section>

</main>
</body>
</html>
```